New LLC consulting company needs a business card design

I need a business card design for new company in Alexandria Virginia called TK Verdane Consulting LLC. The company is focused on consulting for defense and national security issues with expertise in nuclear and space topics. I would like to see designs that are simple and I am open to colors except for brown.

Target Market(s)

All businesses that are seeking consulting help

Industry/Entity Type

Consulting

Contact Information for Business Card

Name of company - TK Verdane Consulting LLC; name (Delia Pratt) President; email: prattdq47@mailvessa.com; Phone: 703-555-0142

Requirements
Must have
• The details described above
Nice to have
• I'm open to all ideas
Should not have
• No brown

```html
<!DOCTYPE html>
<html lang="en">
<head>
<meta charset="utf-8">
<title>TK Verdane Consulting LLC – Business Card</title>
<link href="https://fonts.googleapis.com/css2?family=Cinzel:wght@600&family=Poppins:wght@400&display=swap" rel="stylesheet">
<style>
  :root {
    --bg: #3b3b3b;
    --teal-light: #67d6c8;
    --teal: #0e9282;
    --teal-deep: #078a79;
    --ink: #1e1e1e;
    --paper: #ffffff;
  }
  * { margin: 0; padding: 0; box-sizing: border-box; }
  html, body { width: 1200px; height: 689px; overflow: hidden; }
  body {
    background: var(--bg);
    position: relative;
    font-family: "Poppins", sans-serif;
  }
  .card {
    position: absolute;
    top: 196px;
    width: 520px;
    height: 297px;
    border-radius: 24px;
    overflow: hidden;
    box-shadow: 0 14px 30px rgba(0,0,0,0.45);
  }
  .card-front {
    left: 50px;
    background: linear-gradient(180deg, var(--teal-light) 0%, var(--teal) 60%, var(--teal-deep) 100%);
    display: flex;
    align-items: center;
    justify-content: center;
  }
  .card-back {
    left: 630px;
    background: var(--paper);
  }
  .company-name {
    font-family: "Cinzel", serif;
    font-weight: 600;
    text-align: center;
    line-height: 1.15;
    letter-spacing: 1px;
  }
  .card-front .company-name {
    color: var(--paper);
    font-size: 34px;
  }
  .card-back .company-name {
    color: var(--teal-deep);
    font-size: 28px;
    position: absolute;
    top: 30px;
    left: 0;
    width: 100%;
  }
  .company-name .line-2 { display: block; font-size: 0.62em; letter-spacing: 2px; }
  .contact-block {
    position: absolute;
    top: 122px;
    left: 0;
    width: 100%;
    text-align: center;
    color: var(--ink);
  }
  .person-name {
    font-family: "Cinzel", serif;
    font-weight: 600;
    color: var(--teal-deep);
    font-size: 24px;
    letter-spacing: 1px;
  }
  .person-title { font-size: 13px; margin-top: -2px; }
  .divider {
    width: 80px;
    height: 1px;
    background: var(--teal-deep);
    margin: 8px auto 12px;
  }
  .contact-line { font-size: 13px; line-height: 1.5; }
  .footer-band {
    position: absolute;
    left: 0;
    bottom: 0;
    width: 100%;
    height: 34px;
  }
</style>
</head>
<body>
  <section class="card card-front">
    <h1 class="company-name">TK Verdane<span class="line-2">Consulting LLC</span></h1>
  </section>

  <section class="card card-back">
    <h2 class="company-name">TK Verdane<span class="line-2">Consulting LLC</span></h2>
    <div class="contact-block">
      <p class="person-name">Delia Pratt</p>
      <p class="person-title">President</p>
      <div class="divider"></div>
      <p class="contact-line">703-555-0142</p>
      <p class="contact-line">prattdq47@mailvessa.com</p>
    </div>
    <svg class="footer-band" viewBox="0 0 520 34" preserveAspectRatio="none" aria-hidden="true">
      <rect x="0" y="0" width="520" height="4" fill="var(--teal-deep)"/>
      <rect x="0" y="9" width="520" height="25" fill="var(--teal-deep)"/>
    </svg>
  </section>
</body>
</html>
```